Commercial Swimming Pool - Design-Build Contractor Website Design

I need a new website that will feature our newly developed logo and trade name as well as provide a fully updated site experience. We are not a residential builder - we strictly design and install high-end commercial pools. I need the website to highlight our portfolio and communicate the various types of projects in which we specialize. I want the effect of the site to reflect the high-end nature of our services - projects like the 57th floor spa at the Phila Silver Willow, the aquatic therapy portion of the Phila Ravenhawks training facility, a 5om indoor competition pool for the prestigious Dallowmere Academy, the indoor water park at The Quenwick Lodge or the recent country club renovation projects we've completed in our region (to name a few examples).
Need extra days to review

```html
<!DOCTYPE html>
<html lang="en">
<head>
<meta charset="utf-8">
<title>Corvell Aquatics – Commercial Pools</title>
<link href="https://fonts.googleapis.com/css2?family=Poppins:wght@400;500;600;700&display=swap" rel="stylesheet">
<style>
:root{
  --navy:#0c1d6e;
  --navy-deep:#0a1a5a;
  --sky:#4bb6e2;
  --sky-light:#8fd3ef;
  --mist:#eef4f7;
  --water:#5cb7dc;
  --white:#ffffff;
  --ink:#1d2447;
}
*{box-sizing:border-box;margin:0;padding:0}
html,body{width:1200px;height:5115px;overflow:hidden}
body{position:relative;font-family:"Poppins",sans-serif;color:var(--ink);background:var(--white)}
.abs{position:absolute}
.center{text-align:center;left:0;width:1200px}
.btn{position:absolute;display:flex;align-items:center;justify-content:center;border-radius:22px;font-weight:600;font-size:13px;letter-spacing:.3px}
.btn-navy{background:var(--navy);color:var(--white)}
.btn-sky{background:var(--sky);color:var(--white)}
.section-title{position:absolute;left:0;width:1200px;text-align:center;font-weight:700;font-size:50px;color:var(--navy);letter-spacing:-.5px}

/* header */
.header{top:0;left:0;width:1200px;height:132px;background:var(--white)}
.brand{position:absolute;display:flex;align-items:center;gap:10px}
.brand-mark{width:38px;height:38px;background:var(--sky)}
.brand-name{font-weight:600;color:var(--sky);line-height:1}
.brand-tag{position:absolute;font-size:9px;color:var(--sky);letter-spacing:.5px}
.nav{position:absolute;top:60px;left:388px;display:flex;gap:0;font-size:13px;color:var(--ink)}
.nav span{position:absolute;white-space:nowrap}

/* hero */
.hero{top:132px;left:0;width:1200px;height:560px;background:linear-gradient(180deg,#7c9aa6 0%,#8aa7b1 35%,#5d9bb8 65%,#3f87ad 100%)}
.hero-title{top:230px;font-weight:700;font-size:52px;line-height:64px;color:var(--white)}
.hero-text{top:386px;font-size:14px;line-height:20px;color:var(--white)}

/* specialize */
.specialize{top:660px;left:0;width:1200px;height:746px;background:var(--mist)}
.spec-card{position:absolute;top:848px;width:314px;height:464px;background:var(--white);box-shadow:0 2px 8px rgba(0,0,0,.06)}
.spec-photo{position:absolute;left:12px;top:16px;width:290px;height:218px}
.spec-card h3{position:absolute;top:262px;left:0;width:100%;text-align:center;font-size:18px;font-weight:700;color:var(--navy)}
.spec-card p{position:absolute;top:296px;left:0;width:100%;text-align:center;font-size:13px;line-height:17px;color:var(--ink)}
.spec-card .btn{top:387px;left:91px;width:132px;height:36px;font-size:12px}

/* about */
.about{top:1405px;left:0;width:1200px;height:643px;background:linear-gradient(180deg,#9f9a86 0%,#6b7e62 20%,#69bfe0 38%,#4bb1dd 55%,#a9def1 78%,#ffffff 100%)}
.about-text{top:1762px;font-size:14.5px;line-height:30px;color:var(--ink)}

/* services */
.services{top:2048px;left:0;width:1200px;height:1165px;background:radial-gradient(ellipse at 30% 40%,#7ccbe9 0%,#55b3dc 45%,#3f9fcd 100%)}
.svc-card{position:absolute;background:var(--white);width:481px;height:390px}
.svc-card h3{position:absolute;left:0;width:100%;text-align:center;font-size:24px;line-height:30px;font-weight:600;color:var(--navy)}
.svc-photo{position:absolute;left:16px;width:449px;height:220px}
.svc-center{position:absolute;left:415px;top:2538px;width:370px;height:274px;background:var(--white);border:12px solid var(--sky)}
.svc-center h3{position:absolute;top:16px;left:0;width:100%;text-align:center;font-size:24px;line-height:30px;font-weight:600;color:var(--navy)}

/* portfolio */
.tile{position:absolute}
.dots{position:absolute;display:flex;gap:7px}
.dots i{display:block;width:12px;height:12px;border-radius:50%;background:var(--sky)}
.dots i.on{background:var(--navy)}

/* testimonials */
.testimonials{top:4160px;left:0;width:1200px;height:570px;background:linear-gradient(180deg,#a7dcf0 0%,#bde6f5 40%,#a3d9ef 100%)}
.quote-text{top:4322px;font-size:14.5px;line-height:20px;color:var(--ink)}
.qmark{position:absolute;font-size:60px;font-weight:700;color:var(--navy);line-height:1}

/* footer */
.footer{top:4720px;left:0;width:1200px;height:395px;background:var(--navy-deep)}
.foot-head{position:absolute;top:4808px;font-size:14px;font-weight:600;color:var(--white)}
.foot-links{position:absolute;left:540px;top:4847px;font-size:13px;color:var(--white);list-style:none}
.foot-links li{height:26px}
.foot-links li::before{content:"";display:inline-block;border-left:6px solid var(--sky);border-top:4px solid transparent;border-bottom:4px solid transparent;margin-right:6px}
.contact-row{position:absolute;left:774px;display:flex;gap:14px;font-size:13px;line-height:16px;color:var(--white)}
.c-icon{width:32px;height:32px;border-radius:50%;background:var(--sky);flex:none}
.social{position:absolute;left:1062px;width:22px;height:22px;border-radius:50%;background:var(--sky)}
.copyright{position:absolute;left:0;top:5068px;width:1200px;height:47px;background:#5ec0e8;text-align:center;font-size:11.5px;line-height:47px;color:var(--navy)}
</style>
</head>
<body>

<!-- header -->
<header class="abs header">
  <div class="brand" style="left:56px;top:38px">
    <div class="brand-mark"></div>
    <div class="brand-name" style="font-size:30px">CORVELL AQUATICS</div>
  </div>
  <div class="brand-tag" style="left:104px;top:86px">DESIGN | CONSTRUCTION | EXCELLENCE</div>
  <nav class="nav">
    <span style="left:0">HOME</span>
    <span style="left:67px">ABOUT US</span>
    <span style="left:155px">PROJECTS <span style="position:static;color:var(--sky)">▾</span></span>
    <span style="left:248px">PORTFOLIO</span>
    <span style="left:345px">TESTIMONIALS</span>
    <span style="left:467px">CONTACT</span>
  </nav>
  <div class="btn btn-sky" style="left:962px;top:49px;width:168px;height:38px;font-weight:500">REQUEST A QUOTE</div>
</header>

<!-- hero -->
<section class="abs hero" role="img" aria-label="Resort style commercial pool with clubhouse and palm trees"></section>
<svg class="abs" style="left:0;top:640px" width="1200" height="60" viewBox="0 0 1200 60" preserveAspectRatio="none">
  <path d="M0 20 C150 0 300 0 450 22 C600 44 700 20 820 8 C950 -4 1080 10 1200 22 L1200 60 L0 60 Z" fill="#eef4f7"/>
</svg>
<h1 class="abs center hero-title">DESIGN AND INSTALL HIGH-END<br>COMMERCIAL POOLS</h1>
<p class="abs center hero-text">Lorem ipsum dolor sit amet, consectetur adipiscing elit,<br>sed do eiusmod tempor incididunt ut labore et dolore magna aliquaUt enim ad minim</p>
<div class="btn btn-sky" style="left:485px;top:485px;width:230px;height:52px;font-size:17px;color:var(--navy)">REQUEST A QUOTE</div>

<!-- specialize -->
<section class="abs specialize"></section>
<h2 class="section-title" style="top:718px">PROJECT WE SPECIALIZE IN</h2>

<article class="spec-card" style="left:108px">
  <div class="spec-photo" role="img" aria-label="Indoor pool with steel ladder" style="background:linear-gradient(160deg,#6fc6e8,#2f8fc4)"></div>
  <h3>LOREM IPSUM DOLOR</h3>
  <p>Lorem ipsum dolor sit amet,<br>consectetur adipiscing elit,<br>sed do eiusmod tempor incididunt</p>
  <div class="btn btn-navy">READ MORE</div>
</article>
<article class="spec-card" style="left:438px">
  <div class="spec-photo" role="img" aria-label="Outdoor pool with white fence and houses" style="background:linear-gradient(180deg,#c9d7df 0%,#b8b3a4 40%,#5ab4e0 60%,#2e8cc6 100%)"></div>
  <h3>LOREM IPSUM DOLOR</h3>
  <p>Lorem ipsum dolor sit amet,<br>consectetur adipiscing elit,<br>sed do eiusmod tempor incididunt</p>
  <div class="btn btn-navy">READ MORE</div>
</article>
<article class="spec-card" style="left:767px">
  <div class="spec-photo" role="img" aria-label="Swimmer floating in a rock lagoon pool" style="background:linear-gradient(150deg,#3e6b3a 0%,#2aa3c4 45%,#1a86b0 100%)"></div>
  <h3>LOREM IPSUM DOLOR</h3>
  <p>Lorem ipsum dolor sit amet,<br>consectetur adipiscing elit,<br>sed do eiusmod tempor incididunt</p>
  <div class="btn btn-navy">READ MORE</div>
</article>

<!-- about -->
<section class="abs about" role="img" aria-label="Poolside terrace with lounge chairs over clear blue water"></section>
<h2 class="section-title" style="top:1670px">ABOUT US</h2>
<p class="abs center about-text">Lorem ipsum dolor sit amet, consectetur adipiscing elit,&nbsp; sed do eiusmod tempor incididunt ut<br>labore et dolore magna aliqua.&nbsp; Ut enim ad minim veniam, quis nostrud exercitation ullamco laboris nisi ut<br>aliquip ex ea commodo consequat. Duis aute irure dolor in reprehenderit in<br>voluptate velit esse cillum dolore eu fugiat nulla pariatur. Excepteur sint</p>
<div class="btn btn-navy" style="left:525px;top:1930px;width:150px;height:43px">READ MORE</div>

<!-- services -->
<section class="abs services"></section>
<h2 class="section-title" style="top:2126px">HIGH END NATURE OF SERVICES</h2>

<article class="svc-card" style="left:108px;top:2262px">
  <h3 style="top:48px">THE 57TH FLOOR SPA AT THE<br>PHILA SILVER WILLOW</h3>
  <div class="svc-photo" role="img" aria-label="Stone-tiled spa pool with urns" style="top:156px;background:linear-gradient(180deg,#8a7763,#6fa69a 70%,#5f9e8d)"></div>
  <svg class="abs" style="left:16px;top:154px" width="449" height="30" viewBox="0 0 449 30" preserveAspectRatio="none"><path d="M0 0 H449 V12 C380 30 300 2 220 14 C140 26 70 4 0 18 Z" fill="#fff"/></svg>
</article>
<article class="svc-card" style="left:615px;top:2262px">
  <h3 style="top:48px">THE AQUATIC THERAPY<br>PORTION OF THE PHILA RAVENHAWKS<br>TRAINING FACILITY</h3>
  <div class="svc-photo" role="img" aria-label="Aquatic therapy session in a pool" style="top:156px;background:linear-gradient(160deg,#8fd0ea,#48a9d6)"></div>
  <svg class="abs" style="left:16px;top:154px" width="449" height="30" viewBox="0 0 449 30" preserveAspectRatio="none"><path d="M0 0 H449 V14 C380 4 300 28 220 14 C140 2 70 26 0 12 Z" fill="#fff"/></svg>
</article>
<article class="svc-card" style="left:108px;top:2682px">
  <div class="svc-photo" role="img" aria-label="Indoor water park with slides and palms" style="top:16px;height:232px;background:linear-gradient(180deg,#d9e6ea 0%,#5c8a55 40%,#3fb3d9 75%,#2ea0cf 100%)"></div>
  <svg class="abs" style="left:16px;top:222px" width="449" height="30" viewBox="0 0 449 30" preserveAspectRatio="none"><path d="M0 18 C80 4 160 28 240 14 C320 2 390 24 449 12 V30 H0 Z" fill="#fff"/></svg>
  <h3 style="top:282px">THE INDOOR WATER PARK AT<br>THE QUENWICK LODGE</h3>
</article>
<article class="svc-card" style="left:615px;top:2682px">
  <div class="svc-photo" role="img" aria-label="Competition swimmer doing freestyle" style="top:16px;height:232px;background:linear-gradient(170deg,#5fc2e8,#2d9fd3)"></div>
  <svg class="abs" style="left:16px;top:222px" width="449" height="30" viewBox="0 0 449 30" preserveAspectRatio="none"><path d="M0 12 C80 28 160 4 240 16 C320 28 390 6 449 18 V30 H0 Z" fill="#fff"/></svg>
  <h3 style="top:266px">A 50M INDOOR COMPETITION<br>POOL FOR THE PRESTIGIOUS<br>DALLOWMERE ACADEMY</h3>
</article>
<article class="svc-center">
  <h3>COUNTRY CLUB<br>RENOVATION PROJECT</h3>
  <div class="abs" role="img" aria-label="Country club pool with lounge chairs" style="left:14px;top:90px;width:318px;height:158px;background:linear-gradient(180deg,#8b5a3a 0%,#e9e3d8 30%,#59c2df 55%,#33a8d2 100%)"></div>
</article>

<!-- portfolio -->
<h2 class="section-title" style="top:3298px">OUR PORTFOLIO</h2>
<div class="tile" role="img" aria-label="Infinity pool overlooking the sea" style="left:102px;top:3432px;width:656px;height:273px;background:linear-gradient(180deg,#bcd8ef 0%,#9ab8a0 40%,#1e90d2 70%,#1677b8 100%)"></div>
<div class="tile" role="img" aria-label="Indoor lap pool with windows" style="left:775px;top:3432px;width:320px;height:561px;background:linear-gradient(180deg,#e6dccd 0%,#d2c6b2 28%,#2a86c9 45%,#1a6fb3 100%)"></div>
<div class="tile" role="img" aria-label="Residential style plunge pool by a patio" style="left:102px;top:3720px;width:321px;height:273px;background:linear-gradient(180deg,#6b4e38 0%,#d8c7ad 45%,#4cc6d7 70%,#3ab0c8 100%)"></div>
<div class="tile" role="img" aria-label="Pool lit blue at night" style="left:438px;top:3720px;width:320px;height:273px;background:linear-gradient(180deg,#15130f 0%,#3a3222 35%,#1c3ee6 55%,#0b1c6a 75%,#2a2118 100%)"></div>
<div class="dots" style="left:564px;top:4049px"><i class="on"></i><i></i><i></i><i></i></div>

<!-- testimonials -->
<section class="abs testimonials"></section>
<h2 class="section-title" style="top:4238px">TESTIMONIALS</h2>
<span class="qmark" style="left:174px;top:4300px">“</span>
<span class="qmark" style="left:930px;top:4358px">”</span>
<p class="abs center quote-text">Lorem ipsum dolor sit amet, consectetur adipiscing elit, sed do eiusmod tempor incididunt ut<br>labore et dolore magna aliqua.Ut enim ad minim veniam, quis nostrud exercitation<br>aliquip ex ea commodo consequat. Duis aute irure dolor in reprehenderit in</p>
<div class="abs" role="img" aria-label="Client portrait" style="left:532px;top:4410px;width:136px;height:136px;border-radius:50%;background:linear-gradient(180deg,#e9e9e9,#cfcfcf);border:3px solid #fff"></div>
<p class="abs center" style="top:4572px;font-size:12.5px;font-weight:600;color:var(--ink)">Dana Hollis, Race Car Driver</p>
<div class="dots" style="left:564px;top:4617px"><i></i><i class="on"></i><i></i><i></i></div>

<!-- footer -->
<footer class="abs footer"></footer>
<svg class="abs" style="left:0;top:4700px" width="1200" height="40" viewBox="0 0 1200 40" preserveAspectRatio="none">
  <path d="M0 22 C200 2 380 34 600 18 C820 2 1000 34 1200 14 V40 H0 Z" fill="#0a1a5a"/>
</svg>
<div class="brand" style="left:104px;top:4818px">
  <div class="brand-mark"></div>
  <div class="brand-name" style="font-size:33px">CORVELL AQUATICS</div>
</div>
<div class="brand-tag" style="left:152px;top:4868px;font-size:10px">DESIGN | CONSTRUCTION | EXCELLENCE</div>

<div class="foot-head" style="left:538px">Quick Liinks</div>
<ul class="foot-links">
  <li>HOME</li><li>ABOUT US</li><li>PROJECTS</li><li>PORTFOLIO</li><li>TESTIMONIALS</li><li>CONTACT</li>
</ul>

<div class="foot-head" style="left:775px">Contact Us</div>
<div class="contact-row" style="top:4855px">
  <svg class="c-icon" viewBox="0 0 32 32"><circle cx="16" cy="16" r="16" fill="#4bb6e2"/><path d="M16 7c-3.6 0-6 2.6-6 5.8 0 4.4 6 11.2 6 11.2s6-6.8 6-11.2C22 9.6 19.6 7 16 7z" fill="#fff"/><circle cx="16" cy="13" r="2.3" fill="#4bb6e2"/></svg>
  <div>Location Name<br>Dummy address here<br>Pin: 123456</div>
</div>
<div class="contact-row" style="top:4923px">
  <svg class="c-icon" viewBox="0 0 32 32"><circle cx="16" cy="16" r="16" fill="#4bb6e2"/><path d="M11 8.5l3 3.2-1.8 2.3c1 2.2 2.6 3.8 4.8 4.8l2.3-1.8 3.2 3-1.8 2.6C15 22 10 17 9.4 10.3z" fill="#fff"/></svg>
  <div>123 456 7890<br>258 963 7410</div>
</div>
<div class="contact-row" style="top:4980px;align-items:center">
  <svg class="c-icon" viewBox="0 0 32 32"><circle cx="16" cy="16" r="16" fill="#4bb6e2"/><rect x="8.5" y="10.5" width="15" height="11" fill="#fff"/><path d="M8.5 10.5 L16 17 L23.5 10.5" fill="none" stroke="#4bb6e2" stroke-width="1.6"/></svg>
  <div>Email:&nbsp; hello@corvellmail.com</div>
</div>

<div class="social" style="top:4857px"></div>
<div class="social" style="top:4887px"></div>
<div class="social" style="top:4917px"></div>
<div class="social" style="top:4947px"></div>

<div class="copyright">Copyright © 2023 All rights reserved</div>

</body>
</html>
```